Fern Moss Cleaning Tablets needs 4 x labels

We're about to launch a very exciting cleaning product to market and need your help to brand the 4 x bottles. www.fernmossly.com.au will change the way people buy and use household cleaning products whilst significantly reducing the impact on the earth.

The tablets are dropped into the long life recycled plastic bottle, you simply add water, wait for the tab to dissolve and begin cleaning.

Target Market(s)

Women aged between 30 - 65, care for the environment, want to use less plastic, are early adopters and like to try new things. Care about a clean home and using less chemicals. Want less packaging, less plastic, less carbon emissions.

Industry/Entity Type

House Cleaning

Font styles to use
Sans Serif

Requirements
Must have
• Each label must have an obvious colour differentiator and each label must be identical in it's dimensions and information. Should look uniform when all 4 bottles are aligned in the cupboard. Limited / no images apart from logo.
Nice to have
• Simple, clear, bold, striking. Limited / no pictures. Clean lines with lots of space.
Should not have
• Sparkwell Pane Label must have a strip of blue (hex BAE1FF).
Grime Hauler Kitchen Cleaner must have a strip of colour (FFD6F3)
The Fizzer Bathroom cleaner must have a colour strip hex # FFFFBA
The Allrounder Multip Purpose must have a strip of colour Hex #BAFFC9

```html
<!DOCTYPE html>
<html lang="en">
<head>
<meta charset="utf-8">
<title>Fern Moss Cleaning Tablets – Label Range</title>
<link rel="stylesheet" href="https://fonts.googleapis.com/css2?family=Antonio:wght@500;600;700&display=swap">
<style>
  :root {
    --page: #ffffff;
    --amber-light: #a4561e;
    --amber: #8a4515;
    --amber-dark: #5e2c0a;
    --ink: #0b3a4a;
    --white: #fbf6ee;
    --bathroom: #03eeee;
    --kitchen: #eec8e4;
    --window: #a0d4ee;
    --multi: #8cefb8;
  }
  * { box-sizing: border-box; margin: 0; padding: 0; }
  html, body { width: 1200px; height: 848px; overflow: hidden; background: var(--page); }
  body { font-family: "Antonio", sans-serif; }
  .range {
    position: relative; width: 1200px; height: 848px;
    display: flex; justify-content: center; align-items: center; gap: 40px;
  }
  .label {
    --accent: var(--bathroom);
    position: relative; width: 250px; height: 560px; border-radius: 18px; overflow: hidden;
    background: linear-gradient(90deg, var(--amber-dark) 0%, var(--amber) 18%, var(--amber-light) 50%, var(--amber) 82%, var(--amber-dark) 100%);
    padding: 70px 20px 0;
    display: flex; flex-direction: column;
  }
  .label--bathroom { --accent: var(--bathroom); }
  .label--kitchen { --accent: var(--kitchen); }
  .label--window { --accent: var(--window); }
  .label--multi { --accent: var(--multi); }

  .brand-block { position: relative; height: 136px; flex: none; }
  .brand-block svg, .tagline-block svg { position: absolute; inset: 0; width: 100%; height: 100%; }
  .brand-block path, .tagline-block path { fill: var(--accent); }
  .brand-name {
    position: absolute; left: 22px; top: 36px; width: 120px;
    color: var(--ink); font-weight: 700; font-size: 32px; line-height: 0.95; text-transform: uppercase;
  }
  .product-name {
    flex: none; height: 104px;
    display: flex; flex-direction: column; justify-content: center; align-items: center;
    color: var(--white); font-weight: 700; text-transform: uppercase; text-align: center;
    font-size: 28px; line-height: 1.2; white-space: nowrap;
  }
  .label--multi .product-name { font-size: 23px; }
  .tagline-block { position: relative; height: 136px; flex: none; }
  .tagline {
    position: absolute; right: 10px; top: 40px; text-align: right;
    color: var(--ink); font-weight: 600; font-size: 14px; line-height: 2.1; text-transform: uppercase; white-space: nowrap;
  }
  .label-footer {
    flex: none; display: flex; justify-content: space-between; align-items: baseline;
    padding: 16px 12px 0; font-weight: 600; text-transform: uppercase; white-space: nowrap;
  }
  .origin { color: var(--accent); font-size: 14px; }
  .volume { color: var(--white); font-size: 14px; }
</style>
</head>
<body>
<main class="range">

  <article class="label label--bathroom">
    <div class="brand-block">
      <svg viewBox="0 0 210 136" preserveAspectRatio="none" aria-hidden="true"><path d="M0 0H210C160 20 145 60 142 136H0Z"/></svg>
      <p class="brand-name">Fern Moss</p>
    </div>
    <h2 class="product-name"><span>The Fizzer</span><span>Bathroom</span></h2>
    <div class="tagline-block">
      <svg viewBox="0 0 210 136" preserveAspectRatio="none" aria-hidden="true"><path d="M210 136H0C50 116 65 76 68 0H210Z"/></svg>
      <p class="tagline">One bottle · One tab ·<br>Dissolve · Clean · Repeat ·</p>
    </div>
    <footer class="label-footer"><span class="origin">Torquay · Australia</span><span class="volume">500 мл</span></footer>
  </article>

  <article class="label label--kitchen">
    <div class="brand-block">
      <svg viewBox="0 0 210 136" preserveAspectRatio="none" aria-hidden="true"><path d="M0 0H210C160 20 145 60 142 136H0Z"/></svg>
      <p class="brand-name">Fern Moss</p>
    </div>
    <h2 class="product-name"><span>Grime Hauler</span><span>Kitchen Cleaner</span></h2>
    <div class="tagline-block">
      <svg viewBox="0 0 210 136" preserveAspectRatio="none" aria-hidden="true"><path d="M210 136H0C50 116 65 76 68 0H210Z"/></svg>
      <p class="tagline">One bottle · One tab ·<br>Dissolve · Clean · Repeat ·</p>
    </div>
    <footer class="label-footer"><span class="origin">Torquay · Australia</span><span class="volume">500 мл</span></footer>
  </article>

  <article class="label label--window">
    <div class="brand-block">
      <svg viewBox="0 0 210 136" preserveAspectRatio="none" aria-hidden="true"><path d="M0 0H210C160 20 145 60 142 136H0Z"/></svg>
      <p class="brand-name">Fern Moss</p>
    </div>
    <h2 class="product-name"><span>Sparkwell Window</span><span>Cleaner</span></h2>
    <div class="tagline-block">
      <svg viewBox="0 0 210 136" preserveAspectRatio="none" aria-hidden="true"><path d="M210 136H0C50 116 65 76 68 0H210Z"/></svg>
      <p class="tagline">One bottle · One tab ·<br>Dissolve · Clean · Repeat ·</p>
    </div>
    <footer class="label-footer"><span class="origin">Torquay · Australia</span><span class="volume">500 мл</span></footer>
  </article>

  <article class="label label--multi">
    <div class="brand-block">
      <svg viewBox="0 0 210 136" preserveAspectRatio="none" aria-hidden="true"><path d="M0 0H210C160 20 145 60 142 136H0Z"/></svg>
      <p class="brand-name">Fern Moss</p>
    </div>
    <h2 class="product-name"><span>The Allrounder Multi</span><span>Purpose Cleaner</span></h2>
    <div class="tagline-block">
      <svg viewBox="0 0 210 136" preserveAspectRatio="none" aria-hidden="true"><path d="M210 136H0C50 116 65 76 68 0H210Z"/></svg>
      <p class="tagline">One bottle · One tab ·<br>Dissolve · Clean · Repeat ·</p>
    </div>
    <footer class="label-footer"><span class="origin">Torquay · Australia</span><span class="volume">500 мл</span></footer>
  </article>

</main>
</body>
</html>
```